Kestrel Facilities Business Card Design

We would now like to design business cards with the new Kestrel Facilities logo

Target Market(s)

Professional

Industry/Entity Type

Professional services

Contact Information for Business Card

Employee name, title, phone number, email address, corporate office address and logo.

Font styles to use
Sans Serif

Colors
0054AA
0677BA
7BADD7
CADEEF
E8F1F8

Requirements
Must have
• My logo
Should not have
• any other pictures or images besides my logo

```html
<!DOCTYPE html>
<html lang="en">
<head>
<meta charset="utf-8">
<title>Kestrel Facilities Business Card</title>
<link rel="stylesheet" href="https://fonts.googleapis.com/css2?family=Montserrat:wght@400;500;700&display=swap">
<style>
  :root {
    --navy: #0054AA;
    --blue: #0677BA;
    --sky: #7BADD7;
    --mist: #CADEEF;
    --ice: #E8F1F8;
    --grey: #A7A9AC;
    --ink: #1E1E1E;
    --paper: #FFFFFF;
    --backdrop: #E6E8EB;
  }
  * { margin: 0; padding: 0; box-sizing: border-box; }
  html, body { width: 1200px; height: 1012px; overflow: hidden; }
  body {
    background: var(--backdrop);
    font-family: "Montserrat", sans-serif;
    position: relative;
  }
  .card {
    position: absolute;
    left: 250px;
    width: 700px;
    height: 400px;
    overflow: hidden;
    box-shadow: 0 6px 18px rgba(0,0,0,0.18);
  }
  .card--back { top: 80px; }
  .card--front { top: 532px; background: var(--paper); }

  .back-pattern {
    position: absolute; inset: 0;
    background: linear-gradient(135deg, #4F8FD0 0%, #3E82C8 100%);
  }
  .back-brand {
    position: absolute;
    right: 150px;
    top: 176px;
    display: flex;
    align-items: center;
    gap: 8px;
    color: var(--paper);
    font-weight: 700;
    font-size: 15px;
    letter-spacing: 0.5px;
  }
  .back-brand .mark-square { width: 14px; height: 14px; background: var(--paper); }

  .front-waves { position: absolute; inset: 0; }

  .holder {
    position: absolute;
    left: 40px;
    top: 70px;
    color: var(--paper);
  }
  .holder-name {
    font-weight: 700;
    font-size: 24px;
    text-transform: uppercase;
    letter-spacing: 0.3px;
  }
  .holder-title {
    font-weight: 400;
    font-size: 17px;
    margin-top: 4px;
  }

  .brand {
    position: absolute;
    right: 48px;
    top: 190px;
    display: flex;
    align-items: center;
    gap: 14px;
    color: var(--navy);
    font-weight: 700;
    font-size: 30px;
    line-height: 1.1;
  }
  .brand .mark-square {
    width: 36px; height: 36px;
    background: var(--navy);
  }

  .address {
    position: absolute;
    left: 50px;
    top: 248px;
    font-size: 17px;
    line-height: 1.35;
    color: var(--ink);
  }
  .contact-list {
    position: absolute;
    left: 50px;
    top: 316px;
    list-style: none;
    font-size: 16px;
    line-height: 1.4;
    color: var(--ink);
  }
  .contact-list li { display: flex; align-items: center; gap: 10px; }
  .contact-list svg { width: 14px; height: 14px; flex: none; }
</style>
</head>
<body>

  <section class="card card--back" aria-label="Business card back">
    <div class="back-pattern" role="img" aria-label="Repeating brand pattern in soft blue tones"></div>
    <div class="back-brand"><span class="mark-square"></span>Kestrel Facilities</div>
  </section>

  <section class="card card--front" aria-label="Business card front">
    <svg class="front-waves" viewBox="0 0 700 400" width="700" height="400" aria-hidden="true">
      <defs>
        <linearGradient id="band-fill" x1="0" y1="0" x2="1" y2="0">
          <stop offset="0" stop-color="#0677BA"/>
          <stop offset="0.55" stop-color="#5C97D3"/>
          <stop offset="1" stop-color="#0677BA"/>
        </linearGradient>
      </defs>
      <path d="M0,0 H700 V28 C610,40 540,70 480,140 C420,210 360,190 0,205 Z" fill="url(#band-fill)"/>
      <path d="M0,213 C360,198 430,220 490,145 C550,75 615,48 700,40 V58 C620,66 560,95 505,160 C445,232 370,212 0,222 Z" fill="var(--grey)"/>
      <path d="M0,228 C370,218 455,245 520,170 C580,100 635,78 700,70 V76 C640,85 585,110 528,176 C462,252 372,226 0,232 Z" fill="var(--blue)"/>
    </svg>

    <div class="holder">
      <p class="holder-name">Dara Whitlow</p>
      <p class="holder-title">Co-Founder</p>
    </div>

    <div class="brand"><span class="mark-square"></span><span>Kestrel<br>Facilities</span></div>

    <p class="address">4180 N. Harbor Lane<br>Suite 1204 Elmfield.31</p>

    <ul class="contact-list">
      <li>
        <svg viewBox="0 0 16 16"><path d="M3 1h3l1.5 4-2 1.5a9 9 0 0 0 4 4l1.5-2 4 1.5v3a1 1 0 0 1-1 1A14 14 0 0 1 2 2a1 1 0 0 1 1-1z" fill="var(--blue)"/></svg>
        +254-602-41375
      </li>
      <li>
        <svg viewBox="0 0 16 16"><rect x="1" y="3" width="14" height="10" rx="1" fill="var(--blue)"/><path d="M1.5 4l6.5 5 6.5-5" fill="none" stroke="#fff" stroke-width="1.3"/></svg>
        info@kestrelfacilities.com
      </li>
      <li>
        <svg viewBox="0 0 16 16"><circle cx="8" cy="8" r="7" fill="var(--blue)"/><path d="M1 8h14M8 1c-3 3.5-3 10.5 0 14M8 1c3 3.5 3 10.5 0 14" fill="none" stroke="#fff" stroke-width="1"/></svg>
        www.kestrelfacilities.com
      </li>
    </ul>
  </section>

</body>
</html>
```